VIP Card Design Project

uZorvo is a premium sneaker store selling brand name sneakers like Volta, Rexa, Kembro and etc. ( www.uzorvoshop.com ) We need to design a VIP card to promote one of our discount program called "Uzorvo VIP Band 17", which offers 24% discount off all full-priced items. The idea is because we have a "Peakline Gym center" (peaklinegym.com) next door and we are trying to design a discount program for people going to the fitness center.
The design is for the front of the card. The back will be black and white with benefits information and member information.
The front design need to include our logo, "VIP", "Band 17" and our web address "Uzorvo.com" and Chatterly and quibbr logo.
It will be a plastic card in the size of 3.375x2.125 (bleed size 3.5x2.25)

```html
<!DOCTYPE html>
<html lang="en">
<head>
<meta charset="utf-8">
<title>Uzorvo VIP Band 17 – Card</title>
<link href="https://fonts.googleapis.com/css2?family=Fredoka:wght@600&family=Arimo:wght@400;700&display=swap" rel="stylesheet">
<style>
  :root {
    --stage: #ece8e2;
    --card: #ffffff;
    --green: #3cb44a;
    --green-dark: #1f7a2c;
    --orange: #e9832b;
    --red: #d7262b;
    --band-light: #f2f2f2;
    --band-dark: #c9c9c9;
    --grey-text: #666666;
    --peach: #fbdcc4;
    --ink: #222222;
  }
  * { box-sizing: border-box; margin: 0; padding: 0; }
  html, body { width: 1200px; height: 665px; overflow: hidden; }
  body {
    background: var(--stage);
    font-family: "Arimo", Arial, sans-serif;
    display: flex;
    align-items: center;
    justify-content: center;
    gap: 50px;
  }
  .card {
    position: relative;
    width: 540px;
    height: 340px;
    background: var(--card);
    box-shadow: 0 6px 18px rgba(0,0,0,.25);
    overflow: hidden;
  }

  /* Front */
  .brand-name {
    position: absolute;
    top: 26px; left: 0; right: 0;
    text-align: center;
    font-family: "Fredoka", "Arimo", sans-serif;
    font-weight: 600;
    font-size: 86px;
    line-height: 1;
    color: var(--green);
  }
  .front-band {
    position: absolute;
    left: 0; right: 0; top: 200px; height: 75px;
    background: linear-gradient(to bottom, var(--band-light), var(--band-dark));
  }
  .club-name {
    position: absolute;
    left: 0; right: 0; top: 222px;
    text-align: center;
    font-weight: 700;
    font-size: 26px;
    color: var(--green);
  }
  .product {
    position: absolute;
    width: 118px; height: 78px;
    border: 4px solid var(--red);
    border-radius: 10px;
  }
  .product--one { left: 52px; top: 182px; background: linear-gradient(135deg, #8a8a8a, #d33d3a); }
  .product--two { left: 212px; top: 150px; background: linear-gradient(135deg, #e7e1d6, #d9a23a 60%, #c1452e); }
  .product--three { left: 372px; top: 126px; background: linear-gradient(135deg, #f1ece6, #e07a5b 70%, #8fb6d9); }
  .discount-badge {
    position: absolute;
    top: -22px; right: -18px;
    width: 46px; height: 46px;
    border-radius: 50%;
    background: var(--red);
    color: #fff;
    font-weight: 700;
    text-align: center;
    line-height: 1;
    padding-top: 9px;
  }
  .discount-badge .pct { font-size: 14px; display: block; }
  .discount-badge .word { font-size: 8px; display: block; margin-top: 2px; }
  .social {
    position: absolute;
    right: 16px; top: 204px;
    display: flex; gap: 8px;
    font-size: 10px; font-weight: 700; color: var(--grey-text);
  }
  .social-item { display: flex; align-items: center; gap: 3px; }
  .social-item::before {
    content: ""; width: 8px; height: 8px; background: var(--grey-text);
  }
  .web-address {
    position: absolute;
    left: 0; right: 0; top: 290px;
    display: flex; justify-content: center; align-items: center; gap: 6px;
    font-size: 13px; color: var(--grey-text);
  }
  .web-address svg { width: 11px; height: 11px; }

  /* Back */
  .back-decor {
    position: absolute;
    right: 0; top: 64px; width: 38px; height: 210px;
    background: var(--peach);
  }
  .back-brand {
    position: absolute;
    top: 10px; right: 12px;
    font-family: "Fredoka", "Arimo", sans-serif;
    font-weight: 600;
    font-size: 24px;
    color: #9a9a9a;
  }
  .back-band {
    position: absolute;
    left: 0; right: 0; top: 44px; height: 34px;
    background: linear-gradient(to bottom, var(--band-light), var(--band-dark));
  }
  .benefits-title {
    position: absolute;
    left: 0; right: 0; top: 46px;
    text-align: center;
    font-weight: 700;
    font-size: 22px;
    color: var(--green);
  }
  .benefits {
    position: absolute;
    left: 30px; right: 48px; top: 92px;
    font-size: 10.5px;
    line-height: 1.25;
    color: var(--green);
  }
  .benefits-intro { margin-bottom: 6px; }
  .benefit-list { list-style: none; }
  .benefit-list li { display: flex; gap: 6px; margin-bottom: 7px; padding-left: 8px; }
  .benefit-letter { color: var(--orange); }
  .member-fields {
    position: absolute;
    left: 40px; right: 30px; bottom: 22px;
    display: flex; gap: 16px;
    font-size: 11px; color: var(--ink);
  }
  .member-field { display: flex; align-items: flex-end; gap: 4px; flex: 1; }
  .member-field .line { flex: 1; border-bottom: 1px solid #999; height: 12px; }
</style>
</head>
<body>

<section class="card card--front">
  <div class="brand-name">uZorvo</div>

  <div class="product product--one" role="img" aria-label="Photo of a red and grey running sneaker">
    <div class="discount-badge"><span class="pct">24%</span><span class="word">discount</span></div>
  </div>
  <div class="product product--two" role="img" aria-label="Photo of a white basketball sneaker with orange and blue accents">
    <div class="discount-badge"><span class="pct">24%</span><span class="word">discount</span></div>
  </div>
  <div class="product product--three" role="img" aria-label="Photo of a white and red high-top sneaker">
    <div class="discount-badge"><span class="pct">24%</span><span class="word">discount</span></div>
  </div>

  <div class="front-band"></div>
  <div class="club-name">Uzorvo VIP Band 17</div>

  <div class="social">
    <span class="social-item">quibbr</span>
    <span class="social-item">Chatterly</span>
  </div>

  <div class="web-address">
    <svg viewBox="0 0 12 12" aria-hidden="true"><circle cx="6" cy="6" r="5" fill="none" stroke="#666" stroke-width="1.2"/><path d="M1 6h10M6 1v10" stroke="#666" stroke-width="1"/></svg>
    <span>www.Uzorvo.com</span>
  </div>
</section>

<section class="card card--back">
  <div class="back-decor"></div>
  <div class="back-brand">UZORVO</div>
  <div class="back-band"></div>
  <h2 class="benefits-title">-: Benefits :-</h2>

  <div class="benefits">
    <p class="benefits-intro">The UZORVO Member Program entitles Members to the following benefits:</p>
    <ol class="benefit-list">
      <li><span class="benefit-letter">a.</span><span>20% OFF your entire first purchase after you sign up (Limited Time Offer). Certain items are excluded from this offer. Please see stores for details.</span></li>
      <li><span class="benefit-letter">b.</span><span>10% OFF every purchase while being a member. Certain items are excluded from this offer. Please see stores for details.</span></li>
      <li><span class="benefit-letter">c.</span><span>Additional 10% OFF and FREE SHIPPING when an item is out of stock in store but can be shipped to you from another location.</span></li>
      <li><span class="benefit-letter">d.</span><span>Eligible to purchase exclusive items offered to members only. Purchasing of exclusive items is limited to 1 item per member per 30 days. Please see stores for details.</span></li>
    </ol>
  </div>

  <div class="member-fields">
    <div class="member-field"><span>Member Name :</span><span class="line"></span></div>
    <div class="member-field"><span>Member ID :</span><span class="line"></span></div>
  </div>
</section>

</body>
</html>
```